SavannaPlate Web Page Templates

I need two templates designed for a wholesale food/catering business, one template for the home page and the other for detail pages. The overall template should be a simple, clean and clear design. I have provided the existing logo to which the templates should directly relate.
SavannaPlate supplies food based upon traditional Ghanian recipes to a number of stores across Canberra. In addition, SavannaPlate offers catering for public and private functions across the Canberra region.
The colours in the logo represent the national colours of Ghana (yellow, green, red and black) and the website content will also include traditional Ghanian Kente patterns which will add further colour elements to the site. On this basis, the template design needs to be fairly sparse so as not to compete with the colourful content of the website detail pages.
There is no requirement for specific pages to be designed, as these will be handled in the CMS implementation.
The information provided in the Word document is only designed to provide a sense of the intended content of the website, not as a requirement for specific pages to be produced.

Target Market(s)

Retail/Wholesale food

Number of Pages Required

2 page

Font styles to use
Serif

Colors

Designer to choose colors to be used in the design.

Requirements
Must have
• Template must accommodate a responsive design
• The logo provided will form the cornerstone of the design
Nice to have
• There
Should not have
• Please do not solicit for extra work or for alternative logo design.

```html
<!DOCTYPE html>
<html lang="en">
<head>
<meta charset="utf-8">
<title>SavannaPlate – Home</title>
<link href="https://fonts.googleapis.com/css2?family=Lobster&family=Lato:wght@400;700;900&display=swap" rel="stylesheet">
<style>
:root{
  --red:#d7261e;
  --orange:#f28a1e;
  --orange-deep:#e7731a;
  --gold:#e0a91d;
  --green:#2f8d3a;
  --ink:#1c1c1c;
  --text:#555;
  --muted:#8a8a8a;
  --paper:#ffffff;
  --mist:#eeeeee;
}
*{box-sizing:border-box;margin:0;padding:0}
html,body{width:1200px;height:3128px;overflow:hidden}
body{position:relative;background:var(--paper);font-family:"Lato",sans-serif;color:var(--text)}
.abs{position:absolute}
.brand{font-family:"Lobster",cursive;color:var(--green);font-weight:400}
/* header */
.site-header{left:0;top:0;width:1200px;height:64px;display:flex;align-items:center;justify-content:space-between;padding:0 140px}
.site-header .brand{font-size:34px}
.main-nav{display:flex;gap:26px;align-items:center;font-size:13px;font-weight:700;color:var(--ink)}
.main-nav .home{color:var(--orange);display:flex;align-items:center;gap:6px}
.main-nav .dot{width:16px;height:16px;border-radius:50%;background:var(--ink);display:inline-block}
/* hero */
.hero{left:0;top:64px;width:1200px;height:720px;background:radial-gradient(ellipse at 68% 45%,#7a2a14 0%,#3b1a10 35%,#151111 70%);}
.hero-dots{left:60px;top:282px;display:flex;flex-direction:column;gap:14px}
.hero-dots span{width:10px;height:10px;border-radius:50%;background:#fff;opacity:.85}
.hero-copy{left:160px;top:218px}
.hero-copy h1{font-family:"Lobster",cursive;font-weight:400;color:#fff;font-size:52px;background:rgba(0,0,0,.45);padding:0 14px;display:inline-block}
.hero-copy p{margin-top:10px;color:#fff;font-size:26px;font-weight:700;background:rgba(0,0,0,.45);padding:2px 14px;display:inline-block}
.btn{display:inline-block;border-radius:30px;font-size:13px;font-weight:700;text-transform:uppercase;letter-spacing:.5px;color:#fff}
.hero-copy .btn{margin-top:30px;border:2px solid #fff;padding:12px 24px}
.hero-curve{left:0;top:600px;width:1200px;height:200px}
/* about */
.about{left:200px;top:800px;width:800px;text-align:center}
.about .brand{font-size:56px}
.about h2{font-weight:400;font-size:28px;color:var(--ink);margin-top:8px}
.about p{font-size:14px;line-height:1.75;margin-top:18px;color:var(--text)}
.about .btn{margin-top:28px;background:var(--red);padding:12px 30px}
/* weekly */
.weekly{left:0;top:1140px;width:1200px;height:520px}
.weekly-bg{left:0;top:0;width:1200px;height:520px}
.weekly h2,.offers h2,.gallery h2{font-family:"Lobster",cursive;font-weight:400;text-align:center;width:1200px;left:0}
.weekly h2{top:80px;font-size:56px;line-height:1.05;color:var(--gold)}
.weekly h2 span{color:var(--green)}
.shops{left:130px;top:228px;width:940px;display:flex;justify-content:space-between}
.shop{width:200px;text-align:center}
.shop .photo{width:184px;height:184px;border-radius:50%;border:6px solid var(--orange);margin:0 auto}
.shop h3{font-size:18px;font-weight:900;color:var(--ink);margin-top:18px;line-height:1.3}
.arrow{top:345px;font-size:26px;color:#b9b9b9}
/* gallery */
.gallery h2{top:1735px;font-size:60px;color:var(--orange)}
.tile{border-radius:4px;display:flex;align-items:center;justify-content:center}
.tile span{color:#fff;font-size:22px;font-weight:700;text-shadow:0 1px 3px rgba(0,0,0,.6)}
/* offers */
.offers{left:0;top:2380px;width:1200px;height:510px}
.offers h2{top:140px;font-size:52px;color:var(--green)}
.offer-list{left:130px;top:240px;width:940px;display:flex;justify-content:space-between}
.offer{width:160px;text-align:center}
.offer .photo{width:136px;height:136px;border-radius:50%;border:5px solid #fff;margin:0 auto}
.offer h3{font-size:14px;font-weight:700;color:#fff;margin-top:14px;line-height:1.3}
/* footer */
.footer-row{left:140px;top:2918px;width:920px;display:flex;justify-content:space-between;align-items:center;font-size:17px;color:var(--ink)}
.footer-row .brand{font-size:44px}
.contact{display:flex;align-items:center;gap:12px}
.contact .icon{width:40px;height:40px;border-radius:50%;display:flex;align-items:center;justify-content:center}
.footer-line{left:0;top:3010px;width:1200px;height:1px;background:#ddd}
.footer-nav{left:0;top:3036px;width:1200px;display:flex;justify-content:center;gap:30px;font-size:14px;font-weight:700;color:var(--ink)}
.copyright{left:0;top:3080px;width:1200px;text-align:center;font-size:12px;color:var(--muted)}
</style>
</head>
<body>

<header class="site-header abs">
  <div class="brand">SavannaPlate</div>
  <nav class="main-nav">
    <span class="home"><span class="dot"></span>HOME</span>
    <span>ABOUT US</span><span>SHOP</span><span>GALLERY</span><span>OUR OFFERS</span><span>CONTACT US</span>
    <svg width="14" height="14" viewBox="0 0 14 14"><circle cx="6" cy="6" r="4.5" fill="none" stroke="#f28a1e" stroke-width="1.8"/><line x1="9.5" y1="9.5" x2="13" y2="13" stroke="#f28a1e" stroke-width="1.8"/></svg>
  </nav>
</header>

<section class="hero abs" role="img" aria-label="Glazed chicken wings with sesame seeds and dipping sauce on a dark board"></section>
<div class="hero-dots abs"><span></span><span></span><span></span><span></span></div>
<div class="hero-copy abs">
  <h1>SavannaPlate Supplies</h1><br>
  <p>Sed ut perspiciatis unde omnis istenatus error</p><br>
  <span class="btn">Get started &rsaquo;</span>
</div>
<svg class="hero-curve abs" viewBox="0 0 1200 200" preserveAspectRatio="none">
  <path d="M0 60 Q600 230 1200 60 L1200 200 L0 200Z" fill="#fff"/>
  <path d="M0 56 Q600 226 1200 56" fill="none" stroke="#2f8d3a" stroke-width="4"/>
  <path d="M0 64 Q600 234 1200 64" fill="none" stroke="#e0a91d" stroke-width="4"/>
  <path d="M0 72 Q600 242 1200 72" fill="none" stroke="#d7261e" stroke-width="5"/>
</svg>

<section class="about abs">
  <div class="brand">SavannaPlate</div>
  <h2>SavannaPlate commenced in 2004</h2>
  <p>Coming from Ghana with a passion for cooking, our founder began sharing home-style dishes with friends and neighbours across Canberra. Word spread quickly, and local stores soon asked to stock our freshly made meals every week. Today we still cook each recipe in small batches, using traditional spices and methods handed down through our family kitchen.</p>
  <span class="btn">Read more &rsaquo;</span>
</section>

<section class="weekly abs">
  <svg class="weekly-bg abs" viewBox="0 0 1200 520" preserveAspectRatio="none">
    <path d="M0 40 Q600 -30 1200 40 L1200 480 Q600 540 0 480Z" fill="#eeeeee"/>
  </svg>
  <h2 class="abs">Weekly Available <span>Foods</span><br>in Shops</h2>
  <span class="arrow abs" style="left:100px">&lsaquo;</span>
  <span class="arrow abs" style="left:1086px">&rsaquo;</span>
  <div class="shops abs">
    <div class="shop"><div class="photo" role="img" aria-label="Rice and bean dish in a bowl" style="background:radial-gradient(circle,#e9dcc3,#a8865a)"></div><h3>Kente Corner Curtin</h3></div>
    <div class="shop"><div class="photo" role="img" aria-label="Rich orange stew in a pot" style="background:radial-gradient(circle,#e8892a,#8a3d12)"></div><h3>Ainslie Fresh Market</h3></div>
    <div class="shop"><div class="photo" role="img" aria-label="White fermented corn dough balls" style="background:radial-gradient(circle,#f4f2ee,#b9c4cc)"></div><h3>Deakin Pantry</h3></div>
    <div class="shop"><div class="photo" role="img" aria-label="Spicy grilled chicken pieces" style="background:radial-gradient(circle,#b8401c,#4a1a0c)"></div><h3>Baobab Foods, Braddon</h3></div>
  </div>
</section>

<section class="gallery">
  <h2 class="abs">Our Gallery</h2>
  <div class="tile abs" style="left:140px;top:1848px;width:450px;height:236px;background:linear-gradient(135deg,#3a2a22,#7b3a1e)" role="img" aria-label="Chicken and spinach casserole in a bowl"><span>Chicken and spinach casserole</span></div>
  <div class="tile abs" style="left:140px;top:2094px;width:450px;height:236px;background:linear-gradient(135deg,#8e2f1a,#d4572a)" role="img" aria-label="Spicy beef casserole with peppers"><span>Spicy beef casserole</span></div>
  <div class="tile abs" style="left:600px;top:1848px;width:460px;height:482px;background:radial-gradient(ellipse at 50% 45%,#c89a3a,#7a4a1c 70%,#3a2214)" role="img" aria-label="Black-eyed beans casserole with corn"><span style="margin-top:380px">Black-eyed beans casserole</span></div>
</section>

<section class="offers abs">
  <svg class="abs" style="left:0;top:0" width="1200" height="510" viewBox="0 0 1200 510" preserveAspectRatio="none">
    <defs><linearGradient id="orangeFill" x1="0" y1="0" x2="0" y2="1"><stop offset="0" stop-color="#f28a1e"/><stop offset="1" stop-color="#e7731a"/></linearGradient></defs>
    <path d="M0 110 Q600 -20 1200 110 L1200 510 L0 510Z" fill="url(#orangeFill)"/>
    <path d="M0 96 Q600 -34 1200 96" fill="none" stroke="#2f8d3a" stroke-width="5"/>
    <path d="M0 104 Q600 -26 1200 104" fill="none" stroke="#d7261e" stroke-width="5"/>
  </svg>
  <h2 class="abs">We Also Offer</h2>
  <div class="offer-list abs">
    <div class="offer"><div class="photo" role="img" aria-label="Jollof rice on a plate" style="background:radial-gradient(circle,#e0703a,#8a2e14)"></div><h3>Jollof rice</h3></div>
    <div class="offer"><div class="photo" role="img" aria-label="Black-eyed beans fritters" style="background:radial-gradient(circle,#d6a35c,#7a4a20)"></div><h3>Black-eyed beans fritters</h3></div>
    <div class="offer"><div class="photo" role="img" aria-label="Jar of sweet chilli sauce" style="background:radial-gradient(circle,#f0d9b0,#b0541c)"></div><h3>Home made sweet chilli sauce</h3></div>
    <div class="offer"><div class="photo" role="img" aria-label="Bowl of red chilli sauce" style="background:radial-gradient(circle,#e8352a,#7a1010)"></div><h3>Traditional Ghanaian Chilli sauce</h3></div>
    <div class="offer"><div class="photo" role="img" aria-label="Round coconut cakes" style="background:radial-gradient(circle,#faf6ee,#cfc6b4)"></div><h3>Coconut cakes</h3></div>
  </div>
</section>

<footer>
  <div class="footer-row abs">
    <div class="contact">
      <span class="icon" style="background:var(--ink)"><svg width="22" height="22" viewBox="0 0 22 22"><circle cx="11" cy="11" r="8" fill="none" stroke="#fff" stroke-width="1.6"/><ellipse cx="11" cy="11" rx="3.5" ry="8" fill="none" stroke="#fff" stroke-width="1.4"/><line x1="3" y1="11" x2="19" y2="11" stroke="#fff" stroke-width="1.4"/></svg></span>
      www.savannaplate.com.au
    </div>
    <div class="brand">SavannaPlate</div>
    <div class="contact">
      <span class="icon" style="background:var(--red)"><svg width="22" height="22" viewBox="0 0 22 22"><rect x="3" y="5" width="16" height="12" rx="1.5" fill="none" stroke="#fff" stroke-width="1.6"/><path d="M3 6 L11 12 L19 6" fill="none" stroke="#fff" stroke-width="1.6"/></svg></span>
      hello@savannaplate.com
    </div>
  </div>
  <div class="footer-line abs"></div>
  <nav class="footer-nav abs"><span>HOME</span><span>ABOUT US</span><span>SHOP</span><span>GALLERY</span><span>OUR OFFERS</span><span>CONTACT US</span></nav>
  <p class="copyright abs">Copyright © 2019 SavannaPlate All Rights Reserved. | Privacy policy</p>
</footer>

</body>
</html>
```